Fun, Clean Business Card For Family Focused Travel Agency

I need a business card using specific colors and fonts as in the uploaded files. Ideally, I would like a large image of the logo on the back and all the contact info on the front. Maybe the stars/dots somewhere in a flowy form.

I do want it the contact information to be clear and easy to read. I don't want it to look too busy. Maybe even a bit minimalist.

I plan or ordering the ROUNDED CORNER business cards from Cardwell Press, so please consider that in your design.

Target Market(s)

Families with children, couples, groups of friends

Contact Information for Business Card

Marla Quint, Owner
Marla@TumbleTrips.example
Cell Phone Number 555-218-4603
Office Phone Number 555-647-1925
Specializing in Glimmerland destinations, Pelican Bay Fun Park, Cruises and All-Inclusive Vacations.

Nice but not required:
www.TumbleTrips.example
plain circle, plain circle, plain circle icons with username: TumbleTrips

Font styles to use
Sans Serif

Requirements
Must have
• Please try to use the colors from the logo as much as possible. I understand lighter shades/colors may be needed for some things.
Should not have
• NO SERIF FONTS. That is really the only thing I do not want at all

```html
<!DOCTYPE html>
<html lang="en">
<head>
<meta charset="utf-8">
<title>Tumble Trips – Business Card</title>
<link rel="stylesheet" href="https://fonts.googleapis.com/css2?family=Work+Sans:wght@400;500;600&display=swap">
<style>
  :root {
    --page: #e4e5ea;
    --card-white: #ffffff;
    --navy: #0f1431;
    --ink: #1b1f3a;
    --orange: #ee7d1e;
    --teal: #2aa7a0;
    --soft-white: #e9e9ee;
    --muted: #c9cad4;
  }
  * { box-sizing: border-box; margin: 0; padding: 0; }
  html, body {
    width: 1200px; height: 900px; overflow: hidden;
    background: var(--page);
    font-family: "Work Sans", Arial, sans-serif;
    color: var(--ink);
  }
  .sheet {
    width: 1200px; height: 900px;
    display: flex; flex-direction: column; align-items: center; justify-content: center;
    gap: 30px;
  }
  .card {
    position: relative;
    width: 700px; height: 400px;
    border-radius: 18px;
    overflow: hidden;
    box-shadow: 0 10px 28px rgba(15, 20, 49, 0.18);
  }

  /* Front */
  .card-front { background: var(--card-white); }
  .brand {
    position: absolute; left: 48px; top: 44px;
    display: flex; align-items: center; gap: 14px;
  }
  .brand-dot {
    width: 46px; height: 46px; border-radius: 50%;
    background: var(--teal);
  }
  .brand-name {
    font-size: 38px; font-weight: 600; color: var(--ink); letter-spacing: 0.5px;
  }
  .divider {
    position: absolute; left: 48px; right: 58px; top: 196px;
    height: 2px; background: var(--orange);
  }
  .edge-tab {
    position: absolute; right: 0; top: 180px;
    width: 16px; height: 34px; background: var(--orange);
  }
  .person {
    position: absolute; right: 58px; top: 128px; text-align: right;
  }
  .person-name {
    font-size: 30px; font-weight: 500; color: var(--orange);
    letter-spacing: 1.5px; text-transform: uppercase; line-height: 1.1;
  }
  .person-role { font-size: 17px; color: var(--ink); margin-top: 4px; }
  .contacts {
    position: absolute; left: 48px; top: 232px;
    list-style: none; font-size: 17px; line-height: 30px;
  }
  .contacts li { display: flex; align-items: center; gap: 12px; }
  .contacts svg { width: 14px; height: 14px; flex: none; }
  .accent { color: var(--orange); }
  .social {
    position: absolute; right: 58px; bottom: 40px;
    display: flex; align-items: center; gap: 10px;
    font-size: 18px;
  }
  .social-handle { margin-right: 6px; }
  .social-dot { width: 22px; height: 22px; border-radius: 50%; background: var(--navy); }
  .social-dot.alt { background: var(--orange); }
  .social-dot.cool { background: var(--teal); }

  /* Back */
  .card-back {
    background: var(--navy);
    display: flex; flex-direction: column; align-items: center; justify-content: center;
    gap: 34px;
  }
  .back-brand { display: flex; align-items: center; gap: 22px; }
  .back-brand .brand-dot { width: 84px; height: 84px; background: var(--soft-white); }
  .back-brand .brand-name { font-size: 70px; color: var(--soft-white); }
  .tagline {
    width: 540px; text-align: center;
    font-size: 18px; line-height: 28px; color: var(--muted);
  }
</style>
</head>
<body>
<main class="sheet">
  <section class="card card-front" aria-label="Card front">
    <div class="brand">
      <span class="brand-dot"></span>
      <span class="brand-name">Tumble Trips</span>
    </div>

    <div class="person">
      <div class="person-name">Marla Quint</div>
      <div class="person-role">Owner</div>
    </div>
    <div class="divider"></div>
    <div class="edge-tab"></div>

    <ul class="contacts">
      <li>
        <svg viewBox="0 0 14 14" aria-hidden="true"><rect x="3.5" y="1" width="7" height="12" rx="1.5" fill="none" stroke="var(--orange)" stroke-width="1.4"/></svg>
        555-218-4603
      </li>
      <li>
        <svg viewBox="0 0 14 14" aria-hidden="true"><path d="M3 1.5l2.5 0.5 1 3-1.6 1.2a7 7 0 0 0 3 3l1.2-1.6 3 1 0.5 2.5c-1 1-2 1.3-3 1A11 11 0 0 1 2 4.5c-0.3-1 0-2 1-3z" fill="var(--orange)"/></svg>
        555-647-1925
      </li>
      <li>
        <svg viewBox="0 0 14 14" aria-hidden="true"><rect x="1" y="3" width="12" height="8.5" rx="1" fill="none" stroke="var(--orange)" stroke-width="1.4"/><path d="M1.5 3.5L7 8l5.5-4.5" fill="none" stroke="var(--orange)" stroke-width="1.4"/></svg>
        Marla@TumbleTrips.example
      </li>
      <li>
        <svg viewBox="0 0 14 14" aria-hidden="true"><circle cx="7" cy="7" r="5.8" fill="none" stroke="var(--orange)" stroke-width="1.4"/><ellipse cx="7" cy="7" rx="2.4" ry="5.8" fill="none" stroke="var(--orange)" stroke-width="1.2"/><path d="M1.5 7h11" stroke="var(--orange)" stroke-width="1.2"/></svg>
        <span>www.<span class="accent">TumbleTrips</span>.example</span>
      </li>
    </ul>

    <div class="social">
      <span class="social-handle">TumbleTrips</span>
      <span class="social-dot"></span>
      <span class="social-dot alt"></span>
      <span class="social-dot cool"></span>
    </div>
  </section>

  <section class="card card-back" aria-label="Card back">
    <div class="back-brand">
      <span class="brand-dot"></span>
      <span class="brand-name">Tumble Trips</span>
    </div>
    <p class="tagline">Specializing in Glimmerland destinations, Pelican Bay Fun Park, Cruises and All-Inclusive Vacations.</p>
  </section>
</main>
</body>
</html>
```